Poster design for - Silver Heron Gathering

To design a dynamic illustrated Silver Heron Gathering poster.
The dates are: 3-5 July 2020
Location: Fennick Meadow, Tarwick, Bedfordshire
www.silverheronmeet.co.uk

Here is some text about the event to give you an idea. You can take elements from it if you like:

A Gathering of Female Energy to Ignite and Embrace the Power of Woman with Mother Earth.

Target Market(s)

Women festival goers.

Industry/Entity Type

Festival

Colors

Designer to choose colors to be used in the design.

Requirements
Must have
• Silver Heron Logo - but this can be altered to look washed out.
• Date, location, website url.
Nice to have
• Earthy, hippy, festival look.

```html
<!DOCTYPE html>
<html lang="en">
<head>
<meta charset="utf-8">
<title>Silver Heron Gathering – Poster</title>
<link rel="stylesheet" href="https://fonts.googleapis.com/css2?family=Cinzel:wght@400;700&family=Nunito:wght@600&display=swap">
<style>
  :root {
    --backdrop: #b1afb3;
    --paper: #ffffff;
    --flame-orange: #ef7d1f;
    --flame-gold: #f6b54a;
    --ember-red: #d9482a;
    --violet: #7d1f86;
    --deep-plum: #5a1464;
    --maroon: #3f0a1c;
    --text-orange: #f08a24;
    --title-gold: #f3b456;
    --frame-line: #f07a2a;
  }
  * { margin: 0; padding: 0; box-sizing: border-box; }
  html, body { width: 1200px; height: 928px; overflow: hidden; }
  body { background: var(--backdrop); position: relative; }

  .poster {
    position: absolute;
    left: 288px; top: 24px;
    width: 624px; height: 880px;
    background:
      linear-gradient(180deg,
        var(--paper) 0%, var(--paper) 14%,
        var(--flame-orange) 30%,
        var(--ember-red) 37%,
        var(--violet) 46%,
        var(--deep-plum) 72%,
        var(--maroon) 100%);
    overflow: hidden;
    font-family: "Cinzel", serif;
    text-align: center;
  }
  .poster__warm-glow {
    position: absolute; inset: 0;
    background: radial-gradient(ellipse 60% 40% at 85% 75%, rgba(200,70,30,0.45), transparent 70%);
  }
  .crowd-illustration {
    position: absolute;
    left: 0; top: 74px;
    width: 100%; height: 236px;
    background: linear-gradient(180deg,
      rgba(246,181,74,0.85) 0%,
      rgba(239,125,31,0.9) 45%,
      rgba(217,72,42,0.4) 80%,
      rgba(217,72,42,0) 100%);
  }
  .frame {
    position: absolute;
    left: 17px; top: 17px; right: 17px; bottom: 15px;
    border: 1px solid var(--frame-line);
  }
  .website {
    position: absolute;
    top: 9px; right: 48px;
    padding: 0 6px;
    background: var(--paper);
    font-family: "Nunito", sans-serif;
    font-weight: 600;
    font-size: 11px;
    letter-spacing: 0.06em;
    color: var(--text-orange);
  }
  .tagline {
    position: absolute;
    left: 0; right: 0; top: 334px;
    font-size: 39px;
    line-height: 40px;
    font-weight: 400;
    color: var(--text-orange);
  }
  .brand {
    position: absolute;
    left: 0; right: 0; top: 558px;
    display: flex; flex-direction: column; align-items: center;
  }
  .brand__circle {
    width: 74px; height: 74px;
    border-radius: 50%;
    background: var(--title-gold);
    opacity: 0.85;
  }
  .brand__name {
    margin-top: 28px;
    font-size: 44px;
    font-weight: 700;
    line-height: 1;
    color: var(--title-gold);
  }
  .details {
    position: absolute;
    left: 0; right: 0; top: 762px;
    font-size: 20px;
    line-height: 26px;
    color: var(--text-orange);
  }
</style>
</head>
<body>
  <main class="poster">
    <div class="poster__warm-glow"></div>
    <div class="crowd-illustration" role="img" aria-label="Silhouetted crowd of women with raised arms in fiery orange and gold"></div>
    <div class="frame"></div>
    <p class="website">www.silverheronmeet.co.uk</p>

    <h1 class="tagline">A gathering of<br>female energy to<br>ignite and embrace<br>the power of woman<br>with mother earth.</h1>

    <div class="brand">
      <div class="brand__circle"></div>
      <p class="brand__name">SILVER HERON</p>
    </div>

    <p class="details">The dates are: 3-5 July 2020<br>Location: Fennick Meadow, Tarwick,<br>Bedfordshire</p>
  </main>
</body>
</html>
```